Commercial Real Estate

We need a business card design for a new commercial real estate business that specializes in apartment building brokerage. Not individual units but the entire complex. We find and represent the owners existing buildings and well as new buyers for those buildings. The design should convey trust, integrity, knowledge and growth. It should be easily read.

Target Market(s)

40 to 65 years old

Industry/Entity Type

Real Estate

```html
<!DOCTYPE html>
<html lang="en">
<head>
<meta charset="utf-8">
<title>Halvorsen Property Investments – Business Card</title>
<link href="https://fonts.googleapis.com/css2?family=Exo+2:wght@400;600&family=Oswald:wght@400&display=swap" rel="stylesheet">
<style>
  :root {
    --bg: #232425;
    --teal: #6fcbc8;
    --teal-deep: #58b4b1;
    --slate: #5d6867;
    --slate-dark: #4b5554;
    --paper: #ffffff;
    --paper-shade: #e9eded;
    --ink: #4f5958;
  }
  * { margin: 0; padding: 0; box-sizing: border-box; }
  html, body { width: 1200px; height: 863px; overflow: hidden; }
  body { background: var(--bg); position: relative; font-family: "Exo 2", sans-serif; }

  .card {
    position: absolute; width: 620px; height: 354px; overflow: hidden;
    box-shadow: 0 14px 30px rgba(0,0,0,.45);
  }
  .card--front { left: 150px; top: 50px; background: var(--teal); }
  .card--back  { left: 430px; top: 456px; background: linear-gradient(90deg, var(--paper-shade), var(--paper) 40%); }

  /* front */
  .front__panel {
    position: absolute; inset: 0;
    background: linear-gradient(90deg, var(--paper-shade), var(--paper) 45%);
    clip-path: polygon(20% 20%, 100% 10%, 100% 56%, 20% 66%);
  }
  .brand { display: flex; align-items: center; gap: 12px; color: var(--ink); font-weight: 600; }
  .brand__mark { width: 18px; height: 18px; background: var(--slate); flex: none; }
  .brand__name { font-size: 26px; line-height: 1.05; letter-spacing: .5px; }
  .front__brand { position: absolute; left: 250px; top: 92px; }
  .front__rule { position: absolute; left: 250px; top: 160px; width: 300px; height: 2px; background: var(--teal); }
  .front__web { position: absolute; left: 330px; top: 262px; color: var(--paper); font-size: 15px; letter-spacing: .5px; }

  /* back */
  .back__teal { position: absolute; inset: 0; background: var(--teal); clip-path: polygon(58% 22%, 100% 0, 100% 100%, 64% 100%); }
  .back__strip { position: absolute; inset: 0; background: var(--teal-deep); clip-path: polygon(58% 22%, 68% 22%, 74% 100%, 64% 100%); }
  .back__band { position: absolute; inset: 0; background: var(--slate); clip-path: polygon(48% 14%, 100% 0, 100% 26%, 52% 38%, 48% 30%); }
  .back__fold { position: absolute; inset: 0; background: var(--slate-dark); clip-path: polygon(48% 30%, 52% 38%, 58% 36%); }
  .back__brand { position: absolute; left: 56px; top: 240px; }
  .person { position: absolute; left: 345px; top: 66px; color: var(--paper); }
  .person__name { font-family: "Oswald", sans-serif; font-size: 28px; letter-spacing: 1px; text-transform: uppercase; line-height: 1; }
  .person__title { font-size: 11px; letter-spacing: 1.5px; text-transform: uppercase; margin-top: 4px; }
  .contacts { position: absolute; left: 410px; top: 156px; list-style: none; }
  .contact { display: flex; align-items: center; gap: 18px; height: 56px; color: var(--paper); font-size: 13px; line-height: 1.3; }
  .contact__icon { width: 34px; height: 34px; border-radius: 50%; background: var(--paper); display: grid; place-items: center; flex: none; }
  .contact__icon svg { width: 18px; height: 18px; fill: var(--teal-deep); stroke: var(--teal-deep); }
</style>
</head>
<body>

<section class="card card--front" aria-label="Business card front">
  <div class="front__panel"></div>
  <div class="brand front__brand">
    <span class="brand__mark"></span>
    <span class="brand__name">Halvorsen<br>Property Investments</span>
  </div>
  <div class="front__rule"></div>
  <p class="front__web">www.halvorsenpi.com</p>
</section>

<section class="card card--back" aria-label="Business card back">
  <div class="back__teal"></div>
  <div class="back__strip"></div>
  <div class="back__band"></div>
  <div class="back__fold"></div>

  <div class="brand back__brand">
    <span class="brand__mark"></span>
    <span class="brand__name">Halvorsen<br>Property Investments</span>
  </div>

  <div class="person">
    <p class="person__name">Daniel Brooks</p>
    <p class="person__title">General Manager</p>
  </div>

  <ul class="contacts">
    <li class="contact">
      <span class="contact__icon"><svg viewBox="0 0 24 24"><path stroke="none" d="M12 2a7 7 0 0 0-7 7c0 5 7 13 7 13s7-8 7-13a7 7 0 0 0-7-7zm0 9.5A2.5 2.5 0 1 1 12 6.5a2.5 2.5 0 0 1 0 5z"/></svg></span>
      <span>42 Linden Park Road, Suite 3,<br>West Hall</span>
    </li>
    <li class="contact">
      <span class="contact__icon"><svg viewBox="0 0 24 24"><path stroke="none" d="M6.6 10.8a15 15 0 0 0 6.6 6.6l2.2-2.2a1 1 0 0 1 1-.25 11.4 11.4 0 0 0 3.6.57 1 1 0 0 1 1 1V20a1 1 0 0 1-1 1A17 17 0 0 1 3 4a1 1 0 0 1 1-1h3.5a1 1 0 0 1 1 1c0 1.25.2 2.45.57 3.57a1 1 0 0 1-.25 1z"/></svg></span>
      <span>014 555 0192<br>014 555 0193</span>
    </li>
    <li class="contact">
      <span class="contact__icon"><svg viewBox="0 0 24 24" fill="none"><g fill="none" stroke-width="1.6"><circle cx="12" cy="12" r="9"/><ellipse cx="12" cy="12" rx="4" ry="9"/><path d="M3 12h18M5 7h14M5 17h14"/></g></svg></span>
      <span>dbrooks@halvorsenpi.com<br>www.halvorsenpi.com</span>
    </li>
  </ul>
</section>

</body>
</html>
```